Business Card Design

I need a business card design for my new business based on Long Island, NY also serving NYC called Pawhaven Retreat. I have built a website with cardmint that can be looked at as a basis for the card. It is pawhavenretreat.com.

I board Labrador Retrievers in my home. Specialize in one breed. Cage free environment. Dogs have full run of home and fenced in property. Pawhaven Retreat is a one-of-a-kind, high-quality dog-boarding provider serving specifically Labrador Retrievers. By working with a dog I am comfortable with, I am able to offer the best care for all pets that come through my door. I work with Lab owners in the Long Island/NYC area to provide an
in-home safe, reliable and fun environment for daycare and overnight stays.

I provide a unique boarding experience for Labrador Retrievers on Long Island. Your Lab should be well mannered, housebroken and good with other dogs. Provided your pet is well mannered and house trained, my boarding services allow dogs to experience a cage-free stay while having free roam of my home and property. This allows owners a unique alternative to a kennel, giving pets the chance to experience a home away from home rather than chain linked fences and cold concrete floors.
As a guest at Pawhaven Retreat, your dog will get:

4-star kibble
Access to my in-ground pool
All-natural snack selection
Companionship of other retrievers including my two
Full run of entire home and fenced-in backyard
Photos AND videos posted to Snapgram so you can see your dog having fun while away
Toys, bones and affection

I think it is important to have a pic of the 3 colored labs below. Also the picture of my own personal labs ..the white one with the black puppy. Maybe some paw prints. If using any imagery that MUST look EXACTLY like labrador retriever no generic dogs. Thank you
Updates

The Back of the Card should have the following: The background should be one of the pictures I sent (white dog in pool or another pic I included) At Pawhaven Retreat your Lab gets: Cage Free Environment Full run of my home and fenced in yard In-ground pool Toys and affection Companionship of other Labrador Retrievers Photos and Videos posted Snapgram of your loved one FRONT OF THE CARD: should include picture of the 3 labs (yellow white brown) OR picture of white dog in pool. Pawhaven Retreat should be in larger font than the rest. the following can be in any order. Tom Pelley Commack, NY in Central Long Island pawhavenretreat.com 631-555-0192

Industry/Entity Type

Environment

Contact Information for Business Card

Pawhaven Retreat
Commack, NY
Tom Pelley
hello@pawhavenretreat.com
631-555-0192

```html
<!DOCTYPE html>
<html lang="en">
<head>
<meta charset="utf-8">
<title>Pawhaven Retreat – Business Card</title>
<link href="https://fonts.googleapis.com/css2?family=Cinzel:wght@400&family=Arimo:wght@400&display=swap" rel="stylesheet">
<style>
  :root {
    --page: #e9e6e1;
    --card: #ffffff;
    --ink: #1a1a1a;
    --grass: #4f9a2c;
    --grass-deep: #2f6e1a;
    --grass-pale: #cddcb8;
    --grass-pale-2: #b9cc9e;
    --icon-green: #4c8a2e;
  }
  html, body {
    margin: 0;
    width: 1200px;
    height: 1023px;
    overflow: hidden;
    background: var(--page);
  }
  .canvas { position: relative; width: 1200px; height: 1023px; }
  .card {
    position: absolute;
    width: 700px;
    height: 400px;
    background: var(--card);
    overflow: hidden;
    box-shadow: 0 6px 18px rgba(0,0,0,0.18);
  }
  .card--front { left: 250px; top: 60px; }
  .card--back { left: 250px; top: 563px; }
  .card__art { position: absolute; inset: 0; }

  .front__name {
    position: absolute; right: 40px; top: 44px;
    font: 400 26px/1 "Arimo", sans-serif; color: var(--ink);
    white-space: nowrap;
  }
  .front__contacts {
    position: absolute; right: 40px; top: 150px;
    font: 400 20px/1.5 "Arimo", sans-serif; color: var(--ink);
    text-align: right;
  }
  .contact { display: flex; align-items: center; justify-content: flex-end; gap: 14px; white-space: nowrap; }
  .contact svg { width: 16px; height: 16px; }
  .front__business {
    position: absolute; right: 32px; bottom: 48px;
    font: 400 28px/1 "Cinzel", serif; color: var(--ink);
    white-space: nowrap;
  }

  .back__list {
    position: absolute; left: 46px; top: 40px; width: 560px;
    margin: 0; padding: 0; list-style: none;
    font: 400 19px/1.22 "Arimo", sans-serif; color: var(--ink);
  }
  .back__list li { position: relative; padding-left: 28px; }
  .back__list li::before {
    content: ""; position: absolute; left: 0; top: 5px;
    width: 12px; height: 12px; border-radius: 50%; background: var(--ink);
  }
</style>
</head>
<body>
<main class="canvas">

  <section class="card card--front" aria-label="Business card front">
    <svg class="card__art" viewBox="0 0 700 400" width="700" height="400">
      <defs>
        <linearGradient id="frontGrass" x1="0" y1="0" x2="1" y2="1">
          <stop offset="0" stop-color="#4f9a2c"/>
          <stop offset="1" stop-color="#2f6e1a"/>
        </linearGradient>
      </defs>
      <circle cx="20" cy="330" r="200" fill="url(#frontGrass)" stroke="#1a1a1a" stroke-width="4"
              role="img" aria-label="Photo of a Labrador puppy playing with a soccer ball on grass"/>
    </svg>
    <div class="front__name">NY Tom Pelley</div>
    <div class="front__contacts">
      <div class="contact">631-555-0192
        <svg viewBox="0 0 16 16" aria-hidden="true"><path d="M4 1l3 3-2 2c1 2 3 4 5 5l2-2 3 3-2 3C7 15 1 9 1 3z" fill="#4c8a2e"/></svg>
      </div>
      <div class="contact">hello@pawhavenretreat.com
        <svg viewBox="0 0 16 16" aria-hidden="true"><rect x="1" y="3" width="14" height="10" fill="#4c8a2e"/><path d="M1 3l7 6 7-6" fill="none" stroke="#fff" stroke-width="1.4"/></svg>
      </div>
    </div>
    <div class="front__business">Pawhaven Retreat Commack</div>
  </section>

  <section class="card card--back" aria-label="Business card back">
    <svg class="card__art" viewBox="0 0 700 400" width="700" height="400">
      <defs>
        <linearGradient id="backGrass" x1="0" y1="0" x2="1" y2="1">
          <stop offset="0" stop-color="#cddcb8"/>
          <stop offset="1" stop-color="#b9cc9e"/>
        </linearGradient>
      </defs>
      <ellipse cx="290" cy="100" rx="420" ry="290" fill="url(#backGrass)" stroke="#1a1a1a" stroke-width="4"
               role="img" aria-label="Faded photo of a Labrador puppy in the grass"/>
    </svg>
    <ul class="back__list">
      <li>4-star kibble</li>
      <li>Access to my in-ground pool</li>
      <li>All-natural snack selection</li>
      <li>Companionship of other retrievers including my two</li>
      <li>Full run of entire home and fenced-in backyard</li>
      <li>Photos AND videos posted to Snapgram so you can see your dog having fun while away</li>
      <li>Toys, bones and affection</li>
    </ul>
  </section>

</main>
</body>
</html>
```